Modern Business Card for Larkwell 2018

Our company assumes the best about people. We are creating an online community of entrepreneurs and business leaders who struggle with marketing their business online.

This business card should POP! We recently got a new logo and are launching a new website next month, so our business cards should make a statement that feels:
-Fresh
-Smart
-Trustworthy
-Fun

Target Market(s)

small business owners, entrepreneurs

Industry/Entity Type

Digital Marketing

Contact Information for Business Card

Dimensions: 3.5" x 2"

Font styles to use
Sans Serif

Colors
f37122
ffffff

Requirements
Must have
• We need a business card with a modern, bold design. We will use one side of the card as a lead-generation offer, so text on one side will need to fit up to 140 characters. The business card should stick to our core colors (orange, black, and white).
Nice to have
• We think a vertical "portrait" design could be interesting.
Should not have
• Should not look like a traditional business card. The round icon should stand out from a distance.

```html
<!DOCTYPE html>
<html lang="en">
<head>
<meta charset="utf-8">
<title>Larkwell Business Card</title>
<link rel="stylesheet" href="https://fonts.googleapis.com/css2?family=Work+Sans:wght@400;500;800&display=swap">
<style>
  :root {
    --orange: #f37122;
    --white: #ffffff;
    --card: #1e1e1e;
    --card-edge: #262626;
    --backdrop: #2b2b2b;
  }
  * { box-sizing: border-box; margin: 0; padding: 0; }
  html, body {
    width: 1200px; height: 900px; overflow: hidden;
    background: var(--backdrop);
    font-family: "Work Sans", Arial, sans-serif;
    color: var(--white);
  }
  .canvas { position: relative; width: 1200px; height: 900px; }
  .card {
    position: absolute; left: 250px; width: 700px; height: 400px;
    background: linear-gradient(135deg, var(--card) 0%, var(--card-edge) 100%);
    box-shadow: 0 12px 30px rgba(0,0,0,.45);
  }
  .card--offer { top: 30px; }
  .card--contact { top: 470px; }

  .brand { display: flex; flex-direction: column; align-items: center; }
  .brand__dot { width: 58px; height: 58px; border-radius: 50%; background: var(--orange); }
  .brand__name {
    font-weight: 800; letter-spacing: 2px; line-height: 1; color: var(--white);
  }

  .card--offer .brand { position: absolute; top: 92px; left: 0; right: 0; }
  .card--offer .brand__name { font-size: 66px; margin-top: 12px; }
  .offer__text {
    position: absolute; top: 252px; left: 0; right: 0;
    text-align: center; font-size: 14px; line-height: 1.35;
  }
  .offer__rule {
    position: absolute; top: 300px; left: 80px; right: 80px;
    height: 1.5px; background: var(--orange);
  }
  .offer__tagline {
    position: absolute; top: 312px; left: 0; right: 0;
    text-align: center; font-size: 16px; font-weight: 500; letter-spacing: .3px;
  }

  .card--contact .brand { position: absolute; top: 108px; left: 40px; width: 340px; }
  .card--contact .brand__name { font-size: 58px; margin-top: 12px; }
  .contact__divider {
    position: absolute; top: 85px; left: 400px; width: 2px; height: 180px;
    background: var(--white);
  }
  .contact { position: absolute; top: 88px; left: 428px; font-size: 17px; line-height: 1.3; }
  .contact__name { color: var(--orange); font-size: 26px; font-weight: 500; letter-spacing: 1.5px; }
  .contact__role { font-size: 17px; margin-bottom: 12px; }
  .contact__address { margin-bottom: 10px; }
  .contact__line { display: flex; align-items: center; gap: 8px; }
  .contact__line svg { width: 12px; height: 12px; flex: none; }
  .accent { color: var(--orange); }
</style>
</head>
<body>
<main class="canvas">
  <section class="card card--offer">
    <div class="brand">
      <span class="brand__dot"></span>
      <span class="brand__name">LARKWELL</span>
    </div>
    <p class="offer__text">Get your free Larkwell<br>Starter Package and our marketing guide today at</p>
    <div class="offer__rule"></div>
    <p class="offer__tagline">REACH MORE PEOPLE. MAKE MORE MONEY. CREATE MORE IMPACT.</p>
  </section>

  <section class="card card--contact">
    <div class="brand">
      <span class="brand__dot"></span>
      <span class="brand__name">LARKWELL</span>
    </div>
    <div class="contact__divider"></div>
    <div class="contact">
      <p class="contact__name">DANA WHITFIELD</p>
      <p class="contact__role">Story Marketing Coach</p>
      <p class="contact__address">BX2040 , 8/21N. Linden Row<br>Harbor city, Calderia</p>
      <p class="contact__line">
        <svg viewBox="0 0 12 12" aria-hidden="true"><path d="M2 1h3l1 3-2 1a7 7 0 0 0 3 3l1-2 3 1v3c-6 0-10-4-10-10z" fill="var(--orange)"/></svg>
        (555) 318-2740
      </p>
      <p class="contact__line">
        <svg viewBox="0 0 12 12" aria-hidden="true"><rect x="1" y="2.5" width="10" height="7" fill="none" stroke="var(--orange)" stroke-width="1.2"/><path d="M1 2.5l5 4 5-4" fill="none" stroke="var(--orange)" stroke-width="1.2"/></svg>
        Dana@larkwellnow.com
      </p>
      <p class="contact__line">
        <svg viewBox="0 0 12 12" aria-hidden="true"><circle cx="6" cy="6" r="5" fill="none" stroke="var(--orange)" stroke-width="1.2"/><path d="M1 6h10M6 1c-3 3-3 7 0 10M6 1c3 3 3 7 0 10" fill="none" stroke="var(--orange)" stroke-width="1"/></svg>
        <span>www.<span class="accent">larkwellnow</span>.com</span>
      </p>
    </div>
  </section>
</main>
</body>
</html>
```